VOR Exterior Coatings

double sided. the front i want the name of the business each word on a new line with the VOR being bigger. id like teal, black and white colors. the back i want my contact info. Flat, no gloss. Something professional and I want to feel the letters bump put of the card. if possible maybe a paint sprayer in corner. not a car paint spray. (no tank on top of gun)
no vehicle paint sprayers. that means no tank on top of the gun. doesn't have to have a sprayer. black/dark background on the front. white back ground on back with info

```html
<!DOCTYPE html>
<html lang="en">
<head>
<meta charset="utf-8">
<title>VOR Exterior Coatings – Business Card</title>
<link href="https://fonts.googleapis.com/css2?family=Open+Sans:wght@400;600;700;800&display=swap" rel="stylesheet">
<style>
  :root {
    --teal: #1fa3a6;
    --ink: #222426;
    --black: #050505;
    --white: #ffffff;
    --backdrop: #e6e7e8;
    --spray-light: #3a3d40;
    --spray-dark: #121314;
  }
  * { box-sizing: border-box; margin: 0; padding: 0; }
  html, body {
    width: 1200px; height: 900px; overflow: hidden;
    background: var(--backdrop);
    font-family: "Open Sans", Arial, sans-serif;
  }
  .canvas {
    position: relative; width: 1200px; height: 900px;
  }
  .card {
    position: absolute; left: 250px; width: 700px; height: 400px;
    box-shadow: 0 6px 18px rgba(0,0,0,0.18);
  }
  .card--front { top: 34px; background: var(--black); }
  .card--back { top: 466px; background: var(--white); }

  /* front */
  .front-brand {
    position: absolute; left: 170px; top: 120px; width: 300px;
    text-align: center; color: var(--white);
  }
  .brand-name {
    font-weight: 800; line-height: 0.9; letter-spacing: -2px;
    display: flex; align-items: center; justify-content: center; gap: 14px;
  }
  .brand-mark {
    display: inline-block; background: var(--teal);
  }
  .front-brand .brand-name { font-size: 96px; }
  .front-brand .brand-mark { width: 18px; height: 18px; }
  .brand-tagline {
    font-weight: 800; letter-spacing: 3px; margin-top: 6px;
  }
  .front-brand .brand-tagline { font-size: 17px; }
  .spray-tool {
    position: absolute; right: 40px; top: 40px; width: 220px; height: 250px;
    border-radius: 10px;
    background: radial-gradient(ellipse at 45% 45%, var(--spray-light), var(--spray-dark) 72%);
  }

  /* back */
  .back-brand {
    position: absolute; left: 0; top: 42px; width: 100%;
    text-align: center; color: var(--ink);
  }
  .back-brand .brand-name { font-size: 132px; }
  .back-brand .brand-mark { width: 22px; height: 22px; }
  .back-brand .brand-tagline { font-size: 23px; margin-top: 4px; }

  .person {
    position: absolute; right: 372px; top: 250px; text-align: right;
  }
  .person-name {
    font-weight: 800; font-size: 27px; color: var(--teal); letter-spacing: 0.5px;
    white-space: nowrap;
  }
  .person-role { font-size: 19px; color: var(--ink); margin-top: 2px; }

  .divider {
    position: absolute; left: 350px; top: 252px; width: 2px; height: 66px;
    background: var(--ink);
  }

  .contact-list {
    position: absolute; left: 372px; top: 248px; list-style: none;
  }
  .contact-item {
    display: flex; align-items: center; gap: 10px;
    font-size: 19px; color: var(--ink); line-height: 25px;
  }
  .contact-icon { width: 16px; height: 16px; fill: var(--teal); flex: none; }

  .address {
    position: absolute; left: 0; bottom: 38px; width: 100%;
    text-align: center; font-size: 19px; color: var(--ink);
  }
</style>
</head>
<body>
<main class="canvas">

  <section class="card card--front" aria-label="Card front">
    <div class="front-brand">
      <div class="brand-name">VOR<span class="brand-mark" aria-hidden="true"></span></div>
      <div class="brand-tagline">EXTERIOR COATINGS</div>
    </div>
    <div class="spray-tool" role="img" aria-label="White line illustration of a paint spray gun misting paint"></div>
  </section>

  <section class="card card--back" aria-label="Card back">
    <div class="back-brand">
      <div class="brand-name">VOR<span class="brand-mark" aria-hidden="true"></span></div>
      <div class="brand-tagline">EXTERIOR COATINGS</div>
    </div>

    <div class="person">
      <div class="person-name">DANIEL REYES</div>
      <div class="person-role">Manager</div>
    </div>

    <div class="divider" aria-hidden="true"></div>

    <ul class="contact-list">
      <li class="contact-item">
        <svg class="contact-icon" viewBox="0 0 24 24" aria-hidden="true"><path d="M6.6 10.8a15.1 15.1 0 0 0 6.6 6.6l2.2-2.2c.3-.3.7-.4 1-.2 1.1.4 2.3.6 3.6.6.6 0 1 .4 1 1V20c0 .6-.4 1-1 1A17 17 0 0 1 3 4c0-.6.4-1 1-1h3.5c.6 0 1 .4 1 1 0 1.3.2 2.5.6 3.6.1.3 0 .7-.2 1z"/></svg>
        555-014-2100
      </li>
      <li class="contact-item">
        <svg class="contact-icon" viewBox="0 0 24 24" aria-hidden="true"><path d="M2 5h20v14H2z M3.5 6.5 12 13l8.5-6.5" fill="none" stroke="currentColor"/><path d="M2 5h20v14H2V5zm2 2v.3l8 6 8-6V7H4z"/></svg>
        hello@vorcoatings.com
      </li>
      <li class="contact-item">
        <svg class="contact-icon" viewBox="0 0 24 24" aria-hidden="true"><circle cx="12" cy="12" r="10"/><path d="M2 12h20M12 2c3 3 3 17 0 20M12 2c-3 3-3 17 0 20" stroke="#fff" stroke-width="1.6" fill="none"/></svg>
        www.vorcoatings.com
      </li>
    </ul>

    <p class="address">Your address, city, state, ZIP 0000</p>
  </section>

</main>
</body>
</html>
```